Corvane Capital Business Cards

These are professional business cards that are for my family office.
Put fake emails and phone numbers as of now until I finalize those components. This family office controls my families investments, assets, and future. The cards should be professional.
..
.
.
.
I just uploaded another variation of a logo I would like to see as a business card to I am inbeteen which logo to use

Target Market(s)

business

Industry/Entity Type

business

Contact Information for Business Card

Professional, wealth related, finance related.

Requirements
Must have
• Logo

```html
<!DOCTYPE html>
<html lang="en">
<head>
<meta charset="UTF-8">
<title>Corvane Capital – Business Cards</title>
<link href="https://fonts.googleapis.com/css2?family=Playfair+Display:wght@500&family=Poppins:wght@400&display=swap" rel="stylesheet">
<style>
  :root {
    --backdrop: #cfcfcf;
    --card-white: #ffffff;
    --card-black: #050505;
    --gold: #c8b074;
    --ink: #111111;
    --edge: #c8b074;
  }
  * { box-sizing: border-box; margin: 0; padding: 0; }
  html, body { width: 1200px; height: 800px; overflow: hidden; }
  body {
    background: var(--backdrop);
    position: relative;
    font-family: "Poppins", sans-serif;
  }
  .card {
    position: absolute;
    top: 240px;
    width: 540px;
    height: 310px;
    border-radius: 20px;
    border: 2px solid var(--edge);
    overflow: hidden;
  }
  .card--front { left: 40px; background: var(--card-white); }
  .card--back { left: 620px; background: var(--card-black); }

  /* Front */
  .band-gold {
    position: absolute; left: 390px; top: 0; width: 150px; height: 110px;
    background: var(--gold);
  }
  .band-black {
    position: absolute; left: 0; top: 130px; width: 380px; height: 110px;
    background: var(--card-black);
    clip-path: polygon(0 0, 100% 0, 88% 100%, 0 100%);
  }
  .holder { position: absolute; left: 34px; top: 40px; }
  .holder__name {
    font-family: "Playfair Display", serif; font-weight: 500;
    font-size: 26px; letter-spacing: 2px; color: var(--ink); line-height: 1;
  }
  .holder__name .surname { color: var(--gold); }
  .holder__title { font-size: 15px; color: var(--ink); margin-top: 6px; }
  .front-mark {
    position: absolute; left: 300px; top: 60px;
    display: flex; align-items: center; gap: 10px;
    font-family: "Playfair Display", serif; font-weight: 500;
    font-size: 17px; letter-spacing: 2px; color: var(--ink);
  }
  .front-mark__dot { width: 14px; height: 14px; border-radius: 50%; background: var(--gold); }
  .contact-list {
    position: absolute; left: 34px; top: 146px; list-style: none;
    display: flex; flex-direction: column; gap: 8px;
  }
  .contact-list li {
    display: flex; align-items: center; gap: 12px;
    color: #ffffff; font-size: 14px; line-height: 1;
  }
  .contact-icon {
    width: 22px; height: 22px; border-radius: 50%; background: var(--gold);
    display: flex; align-items: center; justify-content: center;
  }
  .address {
    position: absolute; left: 34px; top: 254px;
    font-size: 14px; color: var(--ink); line-height: 1.3;
  }

  /* Back */
  .back-mark {
    position: absolute; inset: 0;
    display: flex; flex-direction: column; align-items: center; justify-content: center; gap: 22px;
  }
  .back-mark__dot { width: 46px; height: 46px; border-radius: 50%; background: var(--gold); }
  .back-mark__name {
    font-family: "Playfair Display", serif; font-weight: 500;
    font-size: 40px; letter-spacing: 4px; color: var(--gold);
  }
</style>
</head>
<body>

<section class="card card--front" aria-label="Business card front">
  <div class="band-gold"></div>
  <div class="band-black"></div>

  <div class="holder">
    <p class="holder__name">DANIEL <span class="surname">HARTLEY</span></p>
    <p class="holder__title">Managing Director</p>
  </div>

  <div class="front-mark">
    <span class="front-mark__dot"></span>
    <span>CORVANE CAPITAL</span>
  </div>

  <ul class="contact-list">
    <li>
      <span class="contact-icon">
        <svg width="12" height="12" viewBox="0 0 24 24" aria-hidden="true"><path d="M6.6 10.8a15 15 0 0 0 6.6 6.6l2.2-2.2a1 1 0 0 1 1-.25 11.4 11.4 0 0 0 3.6.6 1 1 0 0 1 1 1V20a1 1 0 0 1-1 1A17 17 0 0 1 3 4a1 1 0 0 1 1-1h3.5a1 1 0 0 1 1 1c0 1.25.2 2.45.6 3.6a1 1 0 0 1-.25 1z" fill="#050505"/></svg>
      </span>
      044-987 654 321
    </li>
    <li>
      <span class="contact-icon">
        <svg width="12" height="12" viewBox="0 0 24 24" aria-hidden="true"><rect x="2" y="5" width="20" height="14" rx="1" fill="none" stroke="#050505" stroke-width="2.4"/><path d="M2 6l10 7 10-7" fill="none" stroke="#050505" stroke-width="2.4"/></svg>
      </span>
      office@corvanemail.com
    </li>
    <li>
      <span class="contact-icon">
        <svg width="12" height="12" viewBox="0 0 24 24" aria-hidden="true"><g fill="none" stroke="#050505" stroke-width="2.2"><circle cx="12" cy="12" r="9"/><ellipse cx="12" cy="12" rx="4" ry="9"/><path d="M3 12h18"/></g></svg>
      </span>
      www.corvanecapital.com
    </li>
  </ul>

  <p class="address">88, Harbour Lane Suite 4<br>10452,Northmere</p>
</section>

<section class="card card--back" aria-label="Business card back">
  <div class="back-mark">
    <span class="back-mark__dot"></span>
    <span class="back-mark__name">CORVANE CAPITAL</span>
  </div>
</section>

</body>
</html>
```